Home Page Design (+50 More Pages To Winning Designer!)

We have a 50+ page website, but we're starting with the home page. The winning designer will get all 50+ pages to design as a 2nd project, so make sure you do your best!

Velorane is in the private jet industry and needs a re-designed website.

We have created the structure for the website and content inside of Frandle.io (THESE ARE ONLY ROUGH A.I. GENERATED WIREFRAMES AND DO NOT NEED TO BE FOLLOWED EXACTLY) - https://www.frandle.io/app/project/K482915_qWmRtZaLs-KDnHoUvvy82QJ5cfhaR61trkwqlDV3Hm

Take the content from the 'Home Page' under the 'Wireframe' tab on the Frandle.io link above, but feel free to re-design the page in a better way as these are only A.I. generated wireframes.

We want a DARK theme.... High quality, luxurious feel, greyscale colors. Attached is a brand guideline (BUT THIS IS NOT A 100% BRAND GUIDELINE, YOU CAN CHANGE COLORS AND FONTS AND MAKE CHANGES IF YOU HAVE BETTER IDEAS) and attached is our logo. We are also attaching some examples of other apps and websites to give you a guideline of what we're looking for for this design project.

The final design MUST communicate luxury using high-quality imagery of large cabin luxurious private jets.
Updates

ENTRIES THAT DO NOT FOLLOW THE PROJECT BRIEF WILL BE AUTOMATICALLY DISCARDED. FOLLOW THE INSTRUCTIONS!

Industry/Entity Type

Travel

Number of Pages Required

1 page

Font styles to use
Sans Serif

Colors

Designer to choose colors to be used in the design.

Requirements
Must have
• Follow wireframe and use content in wireframe (see Frandle.io link)

```html
<!DOCTYPE html>
<html lang="en">
<head>
<meta charset="utf-8">
<title>Velorane — Luxury Private Jet Travel</title>
<link href="https://fonts.googleapis.com/css2?family=Exo+2:wght@300;400;500&family=Inter:wght@400;500;600&display=swap" rel="stylesheet">
<style>
:root{
  --black:#000;
  --ink:#111;
  --dark:#2b2b2b;
  --grey:#5e5e5e;
  --white:#fff;
  --muted:#bdbdbd;
  --star:#f2c200;
}
*{box-sizing:border-box;margin:0;padding:0}
html,body{width:1200px;height:4376px;overflow:hidden}
body{font-family:"Inter",sans-serif;color:var(--white);background:var(--ink)}
.head{font-family:"Exo 2",sans-serif;font-weight:400}
section,header,footer{position:relative;width:1200px;overflow:hidden}
.abs{position:absolute}
.btn{position:absolute;display:flex;align-items:center;justify-content:center;font-size:10px;letter-spacing:.5px;text-transform:uppercase;height:36px;width:120px}
.btn-solid{background:var(--white);color:var(--ink)}
.btn-line{border:1px solid var(--white);color:var(--white)}
.btn-dark{background:var(--ink);color:var(--white)}
.btn-line-dark{border:1px solid var(--ink);color:var(--ink)}
.eyebrow{font-size:9px;letter-spacing:.5px;text-transform:uppercase;display:flex;align-items:center;gap:8px}
.eyebrow::after{content:"";width:48px;height:1px;background:currentColor}
.logo{font-family:"Exo 2",sans-serif;font-weight:400;font-size:28px;display:flex;align-items:center;gap:8px;color:var(--white)}
.logo i{width:14px;height:14px;background:var(--white);display:inline-block}
.ph{position:absolute}

/* hero */
.hero{height:561px;background:#1d1d1d}
.hero-photo{position:absolute;inset:0;background:
  radial-gradient(ellipse 260px 200px at 760px 420px,rgba(150,95,55,.55),rgba(150,95,55,0) 70%),
  radial-gradient(ellipse 420px 260px at 780px 150px,rgba(190,190,190,.55),rgba(120,120,120,0) 75%),
  radial-gradient(ellipse 200px 320px at 930px 300px,rgba(70,55,50,.9),rgba(70,55,50,0) 80%),
  linear-gradient(180deg,#2a2a2a 0%,#444 45%,#2b2b2b 70%,#151515 100%)}
.hero-shade{position:absolute;inset:0;background:linear-gradient(90deg,rgba(20,20,20,.85) 0%,rgba(20,20,20,.5) 40%,rgba(20,20,20,0) 65%)}
.nav{position:absolute;top:14px;left:112px;right:112px;height:32px;display:flex;align-items:center}
.nav ul{display:flex;list-style:none;gap:26px;margin-left:40px;font-size:11px}
.nav li::after{content:" ⌄";font-size:9px}
.inquire{margin-left:auto;border:1px solid var(--white);font-size:10px;padding:8px 30px}
.hero h1{position:absolute;left:112px;top:250px;font-size:44px;line-height:54px;font-weight:400}
.hero p{position:absolute;left:112px;top:366px;width:470px;font-size:11px;line-height:16px}

/* search */
.search{height:136px;background:var(--white);color:var(--ink)}
.search h2{position:absolute;left:112px;top:32px;font-size:18px;font-weight:400}
.trip{position:absolute;top:37px;left:288px;display:flex;gap:20px;font-size:10px;align-items:center}
.trip span{display:flex;align-items:center;gap:6px}
.dot{width:9px;height:9px;border-radius:50%;border:1px solid #999}
.dot.on{background:var(--ink);border-color:var(--ink)}
.field{position:absolute;top:68px;height:31px;border:1px solid #aaa;font-size:10px;color:#888;display:flex;align-items:center;padding:0 10px;justify-content:space-between}
.search-btn{position:absolute;left:920px;top:66px;width:130px;height:34px;background:var(--ink);color:var(--white);font-size:12px;display:flex;align-items:center;justify-content:center}

/* features */
.features{height:228px;background:var(--black)}
.feat{position:absolute;top:54px;width:300px}
.ic{width:60px;height:60px;border-radius:50%;border:1.5px solid var(--white);display:flex;align-items:center;justify-content:center}
.feat h3{font-size:16px;font-weight:400;margin-top:14px}
.feat p{font-size:10.5px;line-height:16px;margin-top:5px}

/* discover */
.discover{height:530px;background:
  radial-gradient(ellipse 260px 200px at 1000px 330px,rgba(40,40,40,.45),rgba(40,40,40,0) 75%),
  radial-gradient(ellipse 500px 200px at 450px 470px,rgba(35,35,35,.55),rgba(35,35,35,0) 75%),
  linear-gradient(180deg,#626262,#4e4e4e)}
.discover h2{position:absolute;left:590px;top:152px;font-size:32px;line-height:40px}
.discover p{position:absolute;left:590px;top:245px;width:440px;font-size:10.5px;line-height:16px}
.bullets{position:absolute;display:flex;gap:10px;font-size:11px}
.bullets span{display:flex;align-items:center;gap:6px}
.bullets span::before{content:"";width:11px;height:11px;border-radius:50%;background:var(--white)}

/* luxury */
.luxury{height:423px;background:linear-gradient(180deg,#2b2b2b,#333)}
.luxury h2{position:absolute;left:112px;top:85px;font-size:30px;line-height:38px}
.luxury .intro{position:absolute;left:610px;top:67px;width:480px;font-size:9.5px;line-height:14px}
.card{position:absolute;top:197px;width:315px;height:164px;border:1px solid #9a9a9a;padding:28px 28px}
.card h3{font-size:15px;font-weight:400;margin-top:14px}
.card p{font-size:10px;line-height:15px;color:var(--muted);margin-top:8px}

/* cta light */
.cta-light{height:238px;background:
  radial-gradient(ellipse 420px 90px at 200px 230px,#c9c9c9,rgba(201,201,201,0) 75%),
  radial-gradient(ellipse 500px 90px at 1000px 230px,#cfcfcf,rgba(207,207,207,0) 75%),
  linear-gradient(180deg,#ffffff 0%,#f5f5f5 55%,#e2e2e2 100%);color:var(--ink);text-align:center}
.cta-light h2{position:absolute;left:0;right:0;top:60px;font-size:30px}
.cta-light p{position:absolute;left:0;right:0;top:108px;font-size:10.5px}

/* experience */
.experience{height:538px;background:linear-gradient(90deg,#5a5a5a,#6e6e6e)}
.experience h2{position:absolute;left:112px;top:136px;font-size:31px;line-height:38px}
.experience .lead{position:absolute;left:112px;top:226px;width:450px;font-size:10px;line-height:15px}
.col{position:absolute;top:288px;width:190px}
.col h4{font-size:13px;font-weight:400;display:flex;align-items:center;gap:6px}
.col h4::before{content:"";width:11px;height:11px;border-radius:50%;background:var(--white)}
.col p{font-size:10px;line-height:14px;margin-left:17px;margin-top:4px}

/* faq */
.faq{height:727px;background:linear-gradient(180deg,#2b2b2b,#333 70%,#2a2a2a)}
.faq h2{position:absolute;left:603px;top:100px;font-size:30px}
.faq .sub{position:absolute;left:603px;top:150px;font-size:10px}
.q{position:absolute;left:603px;width:484px;border:1px solid #bbb;font-size:12px;padding:0 18px;display:flex;align-items:center;justify-content:space-between}
.q b{font-weight:400;font-size:16px}
.qopen{padding:14px 18px;display:block}
.qopen p{font-size:10px;line-height:14px;margin-top:10px;color:#ddd}

/* testimonial */
.testi{height:456px;background:linear-gradient(180deg,#f7f7f7,#e4e4e4);color:var(--ink)}
.testi blockquote{position:absolute;left:112px;top:105px;width:520px;font-family:"Exo 2",sans-serif;font-size:29px;line-height:38px}
.stars{position:absolute;left:112px;top:268px;color:var(--star);font-size:16px;letter-spacing:5px}
.arrows{position:absolute;left:748px;top:325px;width:130px;height:58px;background:#2a2a2a;display:flex;color:var(--white);font-size:22px}
.arrows span{flex:1;display:flex;align-items:center;justify-content:center}
.arrows span:first-child{border-right:1px solid #666}

/* cta dark */
.cta-dark{height:260px;background:
  radial-gradient(ellipse 300px 160px at 250px 200px,rgba(110,85,60,.45),rgba(110,85,60,0) 75%),
  linear-gradient(180deg,#262626,#3a3a3a 55%,#1b1b1b);text-align:center}
.cta-dark h2{position:absolute;left:0;right:0;top:60px;font-size:30px}
.cta-dark p{position:absolute;left:285px;right:285px;top:104px;font-size:9px;line-height:13px}

/* footer */
.footer{height:279px;background:var(--ink)}
.fcol{position:absolute;top:45px}
.fcol h4{font-family:"Exo 2",sans-serif;font-weight:400;font-size:15px;margin-bottom:10px}
.fcol li{list-style:none;font-size:8.5px;line-height:20px;color:#ccc}
.social{position:absolute;left:112px;top:172px;display:flex;gap:10px}
.social span{width:22px;height:22px;border-radius:50%;border:1.5px solid var(--white)}
.legal{position:absolute;left:0;right:0;top:250px;text-align:center;font-size:8px;color:#bbb}
.legal span{margin:0 12px}
</style>
</head>
<body>

<header class="hero">
  <div class="hero-photo" role="img" aria-label="Businessman in a dark suit walking across the tarmac past a large-cabin private jet at sunset"></div>
  <div class="hero-shade"></div>
  <nav class="nav">
    <div class="logo">Velorane<i></i></div>
    <ul>
      <li>Aircraft</li><li>Programs</li><li>Why Velorane</li><li>Lifestyle</li><li>Sustainability</li><li>Resources</li><li>Competitors</li>
    </ul>
    <div class="inquire">INQUIRE ➤</div>
  </nav>
  <h1 class="head">Experience the Ultimate<br>in Luxury Jet Travel</h1>
  <p>Velorane offers fractional jet ownership, jet card programs, private jet lease programs, all access programs, helicopter access programs, and by the seat charter flights. Discover the perfect flight program for your needs.</p>
  <div class="btn btn-solid" style="left:112px;top:434px">Explore</div>
  <div class="btn btn-line" style="left:243px;top:434px">Learn More</div>
</header>

<section class="search">
  <h2 class="head">Search Your Flight</h2>
  <div class="trip"><span><i class="dot on"></i><b style="font-weight:500">Round Trip</b></span><span><i class="dot"></i>One Way</span></div>
  <div class="field" style="left:112px;width:165px">Departure Airport <span>✈</span></div>
  <div class="field" style="left:288px;width:165px">Arrival Airport <span>✈</span></div>
  <div class="field" style="left:465px;width:165px">Departure Date <span>▦</span></div>
  <div class="field" style="left:641px;width:165px">Return Date <span>▦</span></div>
  <div class="field" style="left:817px;width:90px">Pax <span>⌄</span></div>
  <div class="search-btn">Search</div>
</section>

<section class="features">
  <div class="feat" style="left:112px">
    <div class="ic"><svg width="30" height="30" viewBox="0 0 30 30" fill="none" stroke="#fff" stroke-width="1.5"><path d="M4 20l6-4h8l6-6"/><path d="M10 20h10"/><circle cx="20" cy="8" r="3"/></svg></div>
    <h3 class="head">Flexible Ownership Options Available</h3>
    <p>Choose from a variety of ownership programs and enjoy the freedom to fly on your own terms.</p>
  </div>
  <div class="feat" style="left:470px">
    <div class="ic"><svg width="30" height="30" viewBox="0 0 30 30" fill="none" stroke="#fff" stroke-width="1.5"><circle cx="13" cy="9" r="4"/><rect x="8" y="17" width="16" height="9" rx="2"/></svg></div>
    <h3 class="head">Convenient Jet Card Programs</h3>
    <p>Access a fleet of private jets with our exclusive jet card programs, offering flexibility and conve-</p>
  </div>
  <div class="feat" style="left:827px">
    <div class="ic"><svg width="30" height="30" viewBox="0 0 30 30" fill="none" stroke="#fff" stroke-width="1.5"><path d="M6 22l8-8 4 4 6-10"/><path d="M6 14l6 6"/></svg></div>
    <h3 class="head">Flexible Lease Programs</h3>
    <p>Experience the luxury of private jet travel without the commitment with our flexible lease programs.</p>
  </div>
</section>

<section class="discover" aria-label="Faded private jet on a runway in the background">
  <div class="ph" style="left:112px;top:51px;width:297px;height:335px;background:
    radial-gradient(ellipse 90px 150px at 110px 220px,rgba(45,50,65,.85),rgba(45,50,65,0) 80%),
    linear-gradient(160deg,#e4e4e4 0%,#b9b9b9 35%,#8c8378 65%,#b78e5c 100%)" role="img" aria-label="Man in a navy suit and sunglasses standing beside a white private jet"></div>
  <div class="ph" style="left:286px;top:252px;width:241px;height:228px;border:2px solid #ddd;background:
    radial-gradient(ellipse 110px 60px at 120px 110px,#f2f2f2,rgba(242,242,242,0) 80%),
    linear-gradient(180deg,#d6d6d6,#a8a8a8 55%,#3e3e3e)" role="img" aria-label="Black and white front view of a private jet on the runway"></div>
  <div class="eyebrow" style="position:absolute;left:590px;top:130px">Discover</div>
  <h2 class="head">Experience the Luxury of<br>Fractional Jet Ownership</h2>
  <p>With Velorane's fractional jet ownership program, you can enjoy the benefits of private jet travel without the hassle and expense of owning a whole aircraft. Our program offers flexibility, convenience, and access to a fleet of luxurious jets, allowing you to travel in style and comfort.</p>
  <div class="bullets" style="left:590px;top:330px"><span>Flexible Ownership Options</span><span>Convenient Booking Process</span><span>Luxurious Fleet of Jets</span></div>
  <div class="btn btn-solid" style="left:590px;top:368px">Learn More</div>
  <div class="btn btn-line" style="left:723px;top:368px">Sign Up</div>
</section>

<section class="luxury">
  <div class="eyebrow" style="position:absolute;left:112px;top:63px">Luxury</div>
  <h2 class="head">Experience the Ultimate in<br>Private Jet Travel</h2>
  <p class="intro">Velorane offers a wide range of exclusive services to meet your private jet travel needs. From fractional jet ownership to on-demand charter flights, we provide the highest level of luxury and convenience.</p>
  <div class="btn btn-solid" style="left:610px;top:117px">Learn More</div>
  <div class="btn btn-line" style="left:742px;top:117px">Sign Up</div>
  <div class="card" style="left:112px">
    <svg width="30" height="32" viewBox="0 0 30 32" fill="none" stroke="#fff" stroke-width="1.5"><circle cx="15" cy="10" r="7"/><path d="M10 16l-2 14 7-4 7 4-2-14"/></svg>
    <h3 class="head">On-Demand Charter</h3>
    <p>Fly anywhere, anytime with our on-demand charter service.</p>
  </div>
  <div class="card" style="left:443px">
    <svg width="32" height="32" viewBox="0 0 32 32" fill="none" stroke="#fff" stroke-width="1.5"><circle cx="16" cy="16" r="13"/><ellipse cx="16" cy="16" rx="6" ry="13"/><path d="M3 16h26M5 9h22M5 23h22"/></svg>
    <h3 class="head">Global Medical Response &amp; Recovery</h3>
    <p>We provide specialized medical transportation services worldwide.</p>
  </div>
  <div class="card" style="left:773px">
    <svg width="32" height="32" viewBox="0 0 32 32" fill="none" stroke="#fff" stroke-width="1.5"><circle cx="22" cy="10" r="6"/><path d="M18 14L5 27l3 3M9 24l3 3"/></svg>
    <h3 class="head">Fractional Jet Ownership</h3>
    <p>Enjoy the benefits of owning a private jet without the hassles.</p>
  </div>
</section>

<section class="cta-light" role="img" aria-label="Soft cloudscape seen from above">
  <h2 class="head">Experience luxury travel like never before</h2>
  <p>Contact us today to book your exclusive jet experience</p>
  <div class="btn btn-dark" style="left:477px;top:138px">Learn More</div>
  <div class="btn btn-line-dark" style="left:609px;top:138px">Sign Up</div>
</section>

<section class="experience">
  <div class="ph" style="left:835px;top:0;width:365px;height:538px;background:
    radial-gradient(ellipse 200px 120px at 200px 470px,#fafafa,rgba(250,250,250,0) 80%),
    linear-gradient(180deg,#f0f0f0,#cfcfcf 45%,#ededed)" role="img" aria-label="Bright sky and clouds behind a silver private jet in flight"></div>
  <div class="ph" style="left:455px;top:150px;width:745px;height:300px;background:radial-gradient(ellipse 300px 90px at 460px 150px,rgba(215,220,230,.55),rgba(215,220,230,0) 80%)" role="img" aria-label="Silver large-cabin private jet banking through the clouds"></div>
  <div class="eyebrow" style="position:absolute;left:112px;top:114px">Experience</div>
  <h2 class="head">Unparalleled Luxury and<br>Convenience for Private Aviation</h2>
  <p class="lead">Discover the ultimate in luxury and convenience with Velorane. Our exclusive private aviation solutions provide you with unparalleled access to the world of private jets, ensuring a seamless and extraordinary travel experience.</p>
  <div class="col" style="left:112px"><h4>Convenience</h4><p>Enjoy hassle-free travel with our flexible scheduling and personalized services.</p></div>
  <div class="col" style="left:365px"><h4>Luxury</h4><p>Indulge in the lavish amenities and exquisite interiors of our private jets.</p></div>
  <div class="btn btn-solid" style="left:112px;top:379px;height:32px">Learn More</div>
  <div class="btn btn-line" style="left:245px;top:379px;height:32px;width:115px">Sign Up</div>
</section>

<section class="faq">
  <div class="ph" style="left:112px;top:93px;width:409px;height:536px;border:2px solid #bbb;background:
    radial-gradient(ellipse 120px 200px at 200px 260px,rgba(150,150,155,.9),rgba(150,150,155,0) 80%),
    linear-gradient(170deg,#cbbca5 0%,#a89a88 35%,#8a8d96 60%,#6f7b93 80%,#c7b79c 100%)" role="img" aria-label="Woman in a grey blazer on the phone seated in a cream leather private jet cabin"></div>
  <h2 class="head">Frequently</h2>
  <p class="sub">Find answers to common questions about Velorane's services and programs.</p>
  <div class="q" style="top:194px;height:40px">What is Velorane?<b>+</b></div>
  <div class="q qopen" style="top:244px;height:110px">How it works?
    <p>Velorane works by allowing customers to purchase fractional ownership of a private jet, join jet card programs for a set number of flight hours, lease a private jet for a specific period, or access our all access and helicopter programs. We also offer charter flights where customers can book individual seats on private jets.</p></div>
  <div class="q" style="top:367px;height:40px">Why choose Velorane?<b>+</b></div>
  <div class="q" style="top:419px;height:40px">How to book?<b>+</b></div>
  <div class="q" style="top:471px;height:40px">What are the benefits?<b>+</b></div>
  <p class="abs head" style="left:603px;top:533px;font-size:13px">Still have questions?</p>
  <p class="abs" style="left:603px;top:553px;font-size:9px;color:#bbb">Contact us for more information.</p>
  <div class="btn btn-solid" style="left:603px;top:583px;height:32px">Learn More</div>
  <div class="btn btn-line" style="left:736px;top:583px;height:32px;width:115px">Sign Up</div>
</section>

<section class="testi">
  <div class="ph" style="left:673px;top:51px;width:415px;height:330px;background:
    radial-gradient(ellipse 90px 110px at 70px 80px,#2a2a2a,rgba(42,42,42,0) 85%),
    radial-gradient(ellipse 110px 170px at 250px 210px,rgba(75,75,78,.9),rgba(75,75,78,0) 80%),
    linear-gradient(110deg,#4a4a4a,#8a8a8a 40%,#b0aaa2 70%,#7a7a7a)" role="img" aria-label="Man in a grey suit and sunglasses walking beside a private jet engine"></div>
  <blockquote>Velorane's services have exceeded<br>my expectations. The convenience<br>and luxury of flying with them<br>is unmatched.</blockquote>
  <div class="stars">★★★★★</div>
  <p class="abs head" style="left:112px;top:300px;font-size:17px">John Doe</p>
  <p class="abs" style="left:112px;top:326px;font-size:9px">CEO, Acme Corp</p>
  <div class="abs" style="left:255px;top:296px;width:1px;height:52px;background:#999"></div>
  <p class="abs" style="left:285px;top:314px;font-size:14px;font-weight:500">Quillmark</p>
  <div class="arrows"><span>←</span><span>→</span></div>
</section>

<section class="cta-dark" role="img" aria-label="Dim private jet cabin in the background">
  <h2 class="head">Experience luxury travel like never before</h2>
  <p>Discover the ultimate in private jet travel with Velorane. Whether you're looking for fractional jet ownership, jet card programs, private jet lease programs, all access programs, helicopter access programs, or by the seat charter flights, we have the perfect solution for your travel needs.</p>
  <div class="btn btn-solid" style="left:477px;top:146px;height:32px">Book</div>
  <div class="btn btn-line" style="left:609px;top:146px;height:32px;width:115px">Contact</div>
</section>

<footer class="footer">
  <div class="logo" style="position:absolute;left:112px;top:68px">Velorane<i></i></div>
  <p class="abs" style="left:112px;top:145px;font-size:9px">FOLLOW US:</p>
  <div class="social"><span></span><span></span><span></span><span></span></div>
  <div class="fcol" style="left:356px"><h4>About Us</h4><ul><li>Charter</li><li>Fleet</li><li>Destinations</li><li>Pricing</li><li>Contact</li></ul></div>
  <div class="fcol" style="left:500px"><h4>Services</h4><ul><li>Private Jets</li><li>Helicopters</li><li>Jet Cards</li><li>Membership</li><li>FAQ</li></ul></div>
  <div class="fcol" style="left:642px"><h4>Terms</h4><ul><li>TERMS</li><li>Privacy</li><li>Careers</li><li>Press</li><li>Blog</li><li>Support</li></ul></div>
  <div class="fcol" style="left:771px"><h4>Subscribe to Our Newsletter</h4><ul><li>Join our mailing list for the latest updates.</li></ul></div>
  <div class="abs" style="left:771px;top:98px;width:212px;height:32px;border:1px solid #bbb;font-size:9px;color:#ccc;display:flex;align-items:center;padding-left:12px">Enter Your Email</div>
  <div class="abs" style="left:990px;top:98px;width:98px;height:32px;background:var(--white);color:var(--ink);font-size:10px;display:flex;align-items:center;justify-content:center">SUBSCRIBE</div>
  <p class="abs" style="left:771px;top:138px;width:260px;font-size:8px;line-height:12px;color:#ccc">By subscribing, you agree to our Privacy Policy and consent to receive updates.</p>
  <div class="abs" style="left:112px;right:112px;top:236px;height:1px;background:#555"></div>
  <p class="legal"><span>© 2024 Velorane. All rights reserved.</span><span>Privacy Policy</span><span>Terms of Service</span><span>Cookie Settings</span></p>
</footer>

</body>
</html>
```